Design my site www.brieflyledger.com

So here is what I am thinking in terms of design:

https://plenvo.com

https://www.skyluxair.com

http://kalvex.com/harbor-plaza-tower/

I want the theme to be white and blue (royal blue). I attached a paint picture of what I would like the site to look like in terms of placing the text. Generally, what I like about the sites above is that they are simple, you can navigate easily and have some kind of idea of what's going on by looking at the center (picture and motto). Let's establish a clear understanding of how the functional part of the site would look like. Please see the picture attached.

I want to keep it simple: On top would be the Name 'BRIEFLY ledger", somewhere to the right on top on the page would be 'Sign in" button.

In the center would be a picture (maybe a video) with the Motto (on top of it all in capital) OBSERVE NAVIGATE DECIDE and below would be the "sign up now"

Below the picture (like on kalvex.com site) or to the left on top of the page would be "About Us', "Press" "Contact Us' buttons.

Then once the user gets to his page his got 3 tabs " Press Headlines", "Events", " Briefings".

we would keep the same format I only have on the site, but separate for every Tab.

I do not want the user to get distracted. I also want him to be able to access the page though mobile phone and be able to get automatic updates just like Zorvan Pings without having to sign in daily.

The landing page must be minimalist yet with business/corporate feel where users can navigate easily and a "what you see is what you get" approach. You want an image or video (personally I prefer the video.. it does capture the users attention instantly, as long as it is an interesting video), with your taglines in it.

Sections available to public: About Us, Contact Us, Landing Page with Signup Option

Private: Public Sections + User Account Page, Tabs for (Events, Press Headlines, Briefings)

Target Market(s)

PR/media monitoring/diplomatic community

Coding

Coded - Design and coding required

Number of Pages Required

1 page

Font styles to use
Serif
Sans Serif

Colors
0255a3
ec1f27

Requirements
Must have
• a simple landing page, that is user friendly.
Nice to have
• a video with the explanation of how to navigate the site
Should not have
• too many colors, graphs etc.

```html
<!DOCTYPE html>
<html lang="en">
<head>
<meta charset="utf-8">
<title>BRIEFLY ledger — Observe Navigate Decide</title>
<link rel="stylesheet" href="https://fonts.googleapis.com/css2?family=Raleway:wght@500;600;700;800&display=swap">
<style>
  :root {
    --royal-blue: #0255a3;
    --signal-red: #ec1f27;
    --signal-red-dark: #c8141b;
    --white: #ffffff;
    --footer-bg: #1a1a1a;
    --footer-text: #cfcfcf;
    --nav-top: #0a86d8;
    --nav-bottom: #0356a6;
    --city-dark: #2b323a;
    --city-mid: #5d6670;
    --city-light: #8a8f92;
  }
  * { box-sizing: border-box; margin: 0; padding: 0; }
  html, body { width: 1200px; height: 738px; overflow: hidden; background: var(--white); }
  body { font-family: "Raleway", Arial, sans-serif; position: relative; }

  .site-header {
    position: absolute; left: 0; top: 0; width: 1200px; height: 67px;
    background: var(--white);
  }
  .brand {
    position: absolute; left: 76px; top: 16px;
    font-size: 33px; font-weight: 700; line-height: 36px;
    color: var(--royal-blue); letter-spacing: 0.3px;
  }
  .sign-in {
    position: absolute; left: 1015px; top: 15px; width: 111px; height: 40px;
    border-radius: 20px; background: var(--royal-blue); color: var(--white);
    font-size: 14px; font-weight: 700; display: flex; align-items: center; justify-content: center;
    text-decoration: none; letter-spacing: 0.3px;
  }

  .hero {
    position: absolute; left: 0; top: 67px; width: 1200px; height: 591px; overflow: hidden;
  }
  .hero-backdrop {
    position: absolute; inset: 0;
    background:
      linear-gradient(rgba(20,24,30,0.35), rgba(20,24,30,0.35)),
      radial-gradient(ellipse at 50% 15%, #9aa0a2 0%, transparent 55%),
      linear-gradient(180deg, var(--city-light) 0%, var(--city-mid) 35%, var(--city-dark) 75%, #3a3330 100%);
  }
  .motto {
    position: absolute; left: 0; top: 182px; width: 1200px; text-align: center;
    font-size: 62px; font-weight: 800; line-height: 64px; letter-spacing: 2px;
    color: var(--white); white-space: nowrap;
  }
  .sign-up {
    position: absolute; left: 485px; top: 271px; width: 230px; height: 51px;
    border-radius: 26px; background: linear-gradient(180deg, var(--signal-red), var(--signal-red-dark));
    color: var(--white); font-size: 22px; font-weight: 700; text-decoration: none;
    display: flex; align-items: center; justify-content: center;
  }
  .section-nav a {
    position: absolute; top: 483px; width: 284px; height: 58px; border-radius: 29px;
    background: linear-gradient(180deg, var(--nav-top), var(--nav-bottom));
    box-shadow: 0 3px 8px rgba(0,0,0,0.45);
    color: var(--white); font-size: 19px; font-weight: 700; text-decoration: none;
    display: flex; align-items: center; justify-content: center; gap: 10px;
  }
  .section-nav svg { width: 18px; height: 18px; fill: var(--white); }
  .nav-about { left: 130px; }
  .nav-press { left: 459px; }
  .nav-contact { left: 787px; }

  .site-footer {
    position: absolute; left: 0; top: 658px; width: 1200px; height: 80px;
    background: var(--footer-bg);
  }
  .copyright {
    position: absolute; left: 76px; top: 36px;
    font-size: 12px; font-weight: 600; color: var(--footer-text); letter-spacing: 0.2px;
  }
  .social-links { position: absolute; left: 963px; top: 32px; display: flex; gap: 18px; }
  .social-links span {
    width: 18px; height: 18px; border-radius: 3px; background: var(--footer-text); display: block;
  }
</style>
</head>
<body>
  <header class="site-header">
    <div class="brand">BRIEFLY ledger</div>
    <a class="sign-in" href="#">SIGN - IN</a>
  </header>

  <main class="hero">
    <div class="hero-backdrop" role="img" aria-label="Aerial photograph of a dense city skyline at dusk"></div>
    <h1 class="motto">OBSERVE NAVIGATE DECIDE</h1>
    <a class="sign-up" href="#">SIGN UP NOW</a>
    <nav class="section-nav">
      <a class="nav-about" href="#">
        <svg viewBox="0 0 16 16" aria-hidden="true"><circle cx="8" cy="4.5" r="3.5"/><path d="M1.5 16c0-4 2.8-6.5 6.5-6.5s6.5 2.5 6.5 6.5z"/></svg>
        ABOUT US
      </a>
      <a class="nav-press" href="#">
        <svg viewBox="0 0 16 16" aria-hidden="true"><path d="M1 3h8v1.6H2.6v8.8h8.8V9l1.6-1.6V15H1z"/><path d="M12.6 1.2l2.2 2.2-6.6 6.6-2.9.7.7-2.9z"/></svg>
        PRESS
      </a>
      <a class="nav-contact" href="#">
        <svg viewBox="0 0 16 16" aria-hidden="true"><path d="M3.6 1l2.3 3.1-1.4 1.7c.9 2 2.6 3.8 4.7 4.8l1.7-1.4L14 11.4l-1.4 2.9C7 14.4 1.6 9 1.7 3.4z"/></svg>
        CONTACT US
      </a>
    </nav>
  </main>

  <footer class="site-footer">
    <p class="copyright">COPYRIGHT © 2016. BRIEFLY LEDGER. ALL RIGHT RESERVED</p>
    <div class="social-links" aria-label="Social links">
      <span></span><span></span><span></span><span></span><span></span>
    </div>
  </footer>
</body>
</html>
```